Keto Food Brand Needs Packaging Design and Logo

We need a logo and packaging design for a stand-up food bag for our keto shake mix. We are a health and wellness brand launching our first shake mix product. I would like bold, bright colors. This document goes more in depth . This brand might encompass more than only food so I want the logo to be versatile for supplements and other health products. https://files.plavexa.net/doc/k7Rt2mQx9LpW4vZs8NcB3yHf6JdTa1Ue/view?share=link See images of logos attached. It doesn't have to be food for the logo but I like the creativity of the ones listed.

Target Market(s)

Keto. Health and Fitness

Logo Text

Zumora

Font styles to use
Serif
Sans Serif

Colors

Designer to choose colors to be used in the design.

```html
<!DOCTYPE html>
<html lang="en">
<head>
<meta charset="utf-8">
<title>Zumora Keto Cheesecake Shake Mix – Pouch Front</title>
<link href="https://fonts.googleapis.com/css2?family=Outfit:wght@700;800;900&family=Oswald:wght@500;600;700&display=swap" rel="stylesheet">
<style>
  :root {
    --bg: #ececec;
    --teal: #3ec3d4;
    --band: #f3f4f3;
    --ink: #1e2327;
    --navy: #16344a;
    --red: #d8232e;
    --white: #ffffff;
    --cream: #efe3bf;
    --crust: #b7783f;
  }
  * { margin: 0; padding: 0; box-sizing: border-box; }
  html, body {
    width: 1126px; height: 1200px; overflow: hidden;
    background: var(--bg);
  }
  .canvas { position: relative; width: 1126px; height: 1200px; }
  .pouch {
    position: absolute; left: 277px; top: 215px;
    width: 548px; height: 922px;
    background: var(--teal);
    border-radius: 10px;
    overflow: hidden;
  }
  .pouch__band { position: absolute; inset: 0; width: 100%; height: 100%; }
  .brand-name {
    position: absolute; left: 0; width: 100%; top: 168px;
    text-align: center;
    font-family: "Outfit", sans-serif; font-weight: 800;
    font-size: 40px; line-height: 44px; letter-spacing: 1px; color: var(--ink);
  }
  .product-keto {
    position: absolute; left: 184px;
    font-family: "Outfit", sans-serif; font-weight: 800;
    font-size: 196px; line-height: 150px; letter-spacing: -8px;
    color: var(--ink);
  }
  .product-keto--top { top: 262px; }
  .product-keto--bottom { top: 427px; }
  .claims {
    position: absolute; left: 50px; top: 458px; width: 104px;
    font-family: "Oswald", sans-serif; font-weight: 500;
    font-size: 13px; line-height: 15px; color: var(--ink);
    text-align: center; text-transform: uppercase;
  }
  .claims li { list-style: none; padding: 5px 0; }
  .claims li + li { border-top: 2px solid var(--ink); }
  .servings-badge {
    position: absolute; left: 437px; top: 479px;
    width: 62px; height: 62px; border-radius: 50%;
    background: var(--red); border: 3px solid var(--white);
    color: var(--white); text-align: center;
    font-family: "Oswald", sans-serif; font-weight: 700;
    text-transform: uppercase; transform: rotate(-12deg);
    padding-top: 7px;
  }
  .servings-badge__count { display: block; font-size: 24px; line-height: 24px; }
  .servings-badge__label { display: block; font-size: 10px; line-height: 12px; }
  .flavour-photo {
    position: absolute; left: 444px; top: 636px;
    width: 104px; height: 124px;
    border-radius: 18px 0 0 18px;
    background: linear-gradient(180deg, var(--white) 0%, var(--cream) 30%, #f4ebcf 72%, var(--crust) 100%);
  }
  .flavour-name {
    position: absolute; left: 87px; width: 420px; top: 600px;
    text-align: center;
    font-family: "Oswald", sans-serif; font-weight: 700;
    text-transform: uppercase; color: var(--navy);
  }
  .flavour-name__main { display: block; font-size: 52px; line-height: 58px; letter-spacing: 0.5px; }
  .flavour-name__sub { display: block; font-size: 40px; line-height: 44px; }
  .net-weight {
    position: absolute; left: 72px; top: 768px;
    font-family: "Oswald", sans-serif; font-weight: 500;
    font-size: 16px; line-height: 20px; color: var(--ink);
  }
  .supplement-note {
    position: absolute; left: 366px; top: 768px;
    font-family: "Oswald", sans-serif; font-weight: 500;
    font-size: 15px; line-height: 20px; letter-spacing: 0.5px; color: var(--ink);
    text-transform: uppercase;
  }
</style>
</head>
<body>
<div class="canvas">
  <div class="pouch">
    <svg class="pouch__band" viewBox="0 0 548 922" preserveAspectRatio="none" aria-hidden="true">
      <polygon points="0,154 548,54 548,385 0,585" fill="var(--band)"/>
    </svg>

    <div class="brand-name">ZUMORA</div>
    <div class="product-keto product-keto--top">KE</div>
    <div class="product-keto product-keto--bottom">TO</div>

    <ul class="claims">
      <li>No artificial<br>flavors</li>
      <li>All natural</li>
      <li>Keto-friendly &amp;<br>low carb</li>
    </ul>

    <div class="servings-badge">
      <span class="servings-badge__count">20</span>
      <span class="servings-badge__label">Servings</span>
    </div>

    <div class="flavour-name">
      <span class="flavour-name__main">Cheesecake</span>
      <span class="flavour-name__sub">Shake Mix</span>
    </div>

    <div class="flavour-photo" role="img" aria-label="Slice of cheesecake with a splash of milk"></div>

    <div class="net-weight">Net Wt. 1.02 LB.</div>
    <div class="supplement-note">Dietary Supplement</div>
  </div>
</div>
</body>
</html>
```